New Year's card HTML

can you produce a best new years wishes 2018 design in HTML for our website as what I would like to send by email towards my network of candidates / customers ...

It must be wow, inspiring , design, meaningfull... MMM those people care about me, or those people will help me to go the extra mile, to help me to achieve my career goals, Your best move, enhance my possibilities, bring the love back

Target Market(s)

CEo's / CMO's/ HRDirectors network of 450k

Coding

Coded - Design and coding required

Number of Pages Required

1 page

Colors

Designer to choose colors to be used in the design.

Requirements
Must have
• Logo / visual / website adress www.moravintel.com and a call to action
Should not have
• no sound as our business is confidential

```html
<!DOCTYPE html>
<html lang="en">
<head>
<meta charset="utf-8">
<title>Happy New Year 2018 – Moravintel</title>
<link href="https://fonts.googleapis.com/css2?family=Poppins:wght@500;600;700;800&display=swap" rel="stylesheet">
<style>
  :root {
    --paper: #f3f0f0;
    --ink: #1f1e1d;
    --gold-light: #f1d36a;
    --gold: #d6a82c;
    --gold-deep: #a9781a;
    --spark-pink: #f28a9c;
    --spark-teal: #6fd6d6;
    --spark-yellow: #f5d77a;
  }
  * { margin: 0; padding: 0; box-sizing: border-box; }
  html, body {
    width: 1200px;
    height: 620px;
    overflow: hidden;
    background: var(--paper);
  }
  .card {
    position: relative;
    width: 1200px;
    height: 620px;
    background: var(--paper);
    overflow: hidden;
    font-family: "Poppins", sans-serif;
    color: var(--ink);
  }
  .fireworks {
    position: absolute;
    inset: 0 0 auto 0;
    height: 240px;
    background:
      radial-gradient(circle at 165px 60px, rgba(242,138,156,.45), transparent 65px),
      radial-gradient(circle at 55px 175px, rgba(111,214,214,.45), transparent 70px),
      radial-gradient(circle at 270px 40px, rgba(111,214,214,.4), transparent 60px),
      radial-gradient(circle at 60px 60px, rgba(245,215,122,.4), transparent 60px),
      radial-gradient(circle at 1075px 65px, rgba(242,138,156,.45), transparent 65px),
      radial-gradient(circle at 960px 45px, rgba(111,214,214,.4), transparent 62px),
      radial-gradient(circle at 1160px 180px, rgba(111,214,214,.45), transparent 65px),
      radial-gradient(circle at 1165px 60px, rgba(245,215,122,.4), transparent 55px),
      radial-gradient(circle at 600px 30px, rgba(242,138,156,.3), transparent 80px);
  }
  .confetti-floor {
    position: absolute;
    left: 0; right: 0; bottom: 0;
    height: 60px;
    background:
      radial-gradient(ellipse at 280px 60px, rgba(111,214,214,.3), transparent 70px),
      radial-gradient(ellipse at 900px 60px, rgba(242,138,156,.28), transparent 80px);
  }
  .glitter {
    position: absolute;
    left: 285px;
    top: 55px;
    width: 630px;
    height: 560px;
    border-radius: 48% 52% 45% 55% / 50% 46% 54% 50%;
    background: radial-gradient(ellipse at 50% 48%,
      var(--gold-light) 0%, var(--gold) 45%, rgba(169,120,26,.75) 62%, rgba(214,168,44,0) 72%);
  }
  .frame {
    position: absolute;
    left: 358px;
    top: 80px;
    width: 481px;
    height: 481px;
    border: 5px solid var(--ink);
  }
  .greeting {
    position: absolute;
    left: 358px;
    top: 170px;
    width: 481px;
    text-align: center;
  }
  .brand {
    display: inline-flex;
    align-items: center;
    gap: 12px;
    font-weight: 500;
    font-size: 27px;
    letter-spacing: 2px;
    line-height: 1;
    margin-left: 40px;
  }
  .brand-mark {
    width: 18px;
    height: 18px;
    background: var(--ink);
  }
  .headline {
    margin-top: 12px;
    font-weight: 800;
    font-size: 41px;
    line-height: 1;
    letter-spacing: .3px;
  }
  .year {
    margin-top: -6px;
    font-weight: 800;
    font-size: 172px;
    line-height: 1;
    letter-spacing: 2px;
  }
  .wishes {
    position: absolute;
    left: 363px;
    top: 438px;
    width: 471px;
    text-align: center;
  }
  .message {
    font-weight: 600;
    font-size: 17px;
    line-height: 1.35;
  }
  .cta {
    display: inline-block;
    margin-top: 16px;
    padding: 10px 26px;
    background: var(--ink);
    color: var(--gold-light);
    font-weight: 600;
    font-size: 15px;
    letter-spacing: .4px;
    text-decoration: none;
    border-radius: 24px;
  }
  .website {
    position: absolute;
    left: 35px;
    top: 570px;
    font-weight: 500;
    font-size: 18px;
    color: var(--ink);
    text-decoration: none;
  }
</style>
</head>
<body>
  <main class="card">
    <div class="fireworks" role="img" aria-label="Colourful fireworks bursts and confetti across the top"></div>
    <div class="confetti-floor" role="img" aria-label="Scattered confetti streamers along the bottom edge"></div>
    <div class="glitter" role="img" aria-label="Splash of sparkling gold glitter"></div>
    <div class="frame"></div>
    <section class="greeting">
      <div class="brand"><span class="brand-mark"></span>MORAVINTEL</div>
      <h1 class="headline">Happy New Year</h1>
      <p class="year">2018</p>
    </section>
    <section class="wishes">
      <p class="message">Thank you for the trust. This year, let's go<br>the extra mile together towards your goals.</p>
      <a class="cta" href="https://www.moravintel.com">Make your best move &rarr;</a>
    </section>
    <a class="website" href="https://www.moravintel.com">www.moravintel.com</a>
  </main>
</body>
</html>
```